Web Design Project

Psychotherapy and Counselling Practice needs a landing page web design.

My business "Larkfield Advisory" specialises in the treatment of Anxiety and Depression with a holistic approach, endeavouring to unlock the key that holds us to ransom in a life that is imbalanced, frustrating, and ultimately of our own making due to our own perceptions and behaviours.

There is much that impacts us which we cannot change, but we are always in control of how we think, and how we frame our experiences.....learning to challenge those thoughts and behaviours that are destructive and disempowering opens up a world of joyful possibility. Life is about making choices, learn to make wiser and healthier choices.......

Larkfield Advisory has a client base of individual clients but will seek to expand to offer services to the Corporate world by offering an adjunct to employers for established "Wellness Programs".

Larkfield Advisory is a highly professional, ethically bound business, with the needs of the client at the forefront of all we do.

Larkfield Advisory wishes to avoid the usual "jargon driven" psychobabble offered on many counselling web pages. It aims to be stylishly presented, clean in look and with as few "words" as possible and a largely white background (faster loading and more powerful impact of what is stated), those words contained in the webpage should be meaningful, persuasive and have an impact simply at glance. Larkfield does not want , or expect, those prospective clients in need of support , to be reading through volumes of industry driven cliches.

At this point Larkfield is just looking for a high quality landing page. However in time this will likely expand to include other sections such as case studies, video content etc.

Target Market(s)

Those in need of emotional support, suffering mental health issues, and those simply wanting to become self aware supported by a mindful therapist.

Industry/Entity Type

Industry

Requirements
Must have
• The design must incorporate the Larkfield logo and colour schemes found on the attached files.

```html
<!DOCTYPE html>
<html lang="en">
<head>
<meta charset="utf-8">
<title>Larkfield Advisory</title>
<link href="https://fonts.googleapis.com/css2?family=Lato:wght@300;400;700&display=swap" rel="stylesheet">
<style>
  :root {
    --green: #84a814;
    --green-light: #a9d43a;
    --green-mid: #8cc02a;
    --green-dark: #5f8a10;
    --grey-text: #6d6d6d;
    --disc: #646464;
    --disc-dark: #4c4c4c;
    --white: #ffffff;
    --bg-centre: #f4f4f4;
    --bg-edge: #d6d6d6;
  }
  * { margin: 0; padding: 0; box-sizing: border-box; }
  html, body { width: 1200px; height: 711px; overflow: hidden; }
  body {
    position: relative;
    font-family: "Lato", sans-serif;
    background: radial-gradient(ellipse 60% 70% at 50% 50%, var(--bg-centre), var(--bg-edge));
  }

  .brand {
    position: absolute; top: 80px; left: 0; width: 1200px;
    text-align: center; font-weight: 300; font-size: 29px; line-height: 36px;
    letter-spacing: 1px; color: var(--green);
  }

  .nav-band {
    position: absolute; top: 176px; left: 0; width: 1200px; height: 44px;
    background: var(--green);
  }
  .nav {
    position: absolute; left: 205px; top: 0; width: 790px; height: 44px;
    background: linear-gradient(#f3f3f3, #e9e9e9);
    border: 1px solid #cfd9b0;
    display: flex; justify-content: center; align-items: center; gap: 14px;
    list-style: none; padding-left: 8px;
  }
  .nav li {
    font-weight: 300; font-size: 18px; letter-spacing: -0.8px;
    color: var(--grey-text);
  }
  .nav li.current { color: var(--green); position: relative; }
  .nav li.current::before {
    content: ""; position: absolute; left: -11px; top: 4px;
    width: 7px; height: 7px; border-radius: 50%;
    background: var(--green);
  }

  .feature {
    position: absolute; top: 276px; width: 250px; height: 220px;
  }
  .feature .artwork {
    position: absolute; left: 20px; top: 50px; width: 228px; height: 158px;
    border-radius: 6px;
    background: radial-gradient(ellipse at 45% 55%, var(--green-mid), rgba(140,192,42,0.55) 60%, rgba(140,192,42,0) 100%);
  }
  .feature .shadow {
    position: absolute; left: 10px; top: 202px; width: 210px; height: 16px;
    border-radius: 50%;
    background: radial-gradient(rgba(0,0,0,0.16), transparent 70%);
  }
  .feature .disc {
    position: absolute; left: 0; top: 0; width: 194px; height: 194px;
    border-radius: 50%;
    background: radial-gradient(circle at 50% 35%, var(--disc), var(--disc-dark));
    box-shadow: 0 3px 6px rgba(0,0,0,0.35);
    color: var(--white); text-align: center;
    padding: 0 20px;
  }
  .disc h2 {
    margin-top: 29px; font-size: 20px; line-height: 24px; font-weight: 700; letter-spacing: -1px;
    text-shadow: 0 1px 2px rgba(0,0,0,0.5);
  }
  .disc p {
    margin-top: 12px; font-size: 12px; line-height: 14.5px;
    text-shadow: 0 1px 1px rgba(0,0,0,0.5);
  }
  .disc p.quote { margin-top: 65px; }
  .disc p.author { margin-top: 14px; font-weight: 700; }
  .disc .more {
    position: absolute; left: 50%; transform: translateX(-50%); top: 154px;
    width: 70px; height: 19px; border: 1px solid #bdbdbd; border-radius: 10px;
    font-size: 11px; font-weight: 700; letter-spacing: -0.6px; line-height: 17px;
    color: var(--white); text-decoration: none;
  }
  .about { left: 249px; }
  .quote-card { left: 495px; }
  .services { left: 736px; }

  .social {
    position: absolute; top: 541px; left: 489px; display: flex; gap: 3px;
  }
  .social .icon {
    width: 54px; height: 54px; border-radius: 50%;
    background: radial-gradient(circle at 50% 30%, var(--green-light), var(--green-dark));
    border: 2px solid #9fc53a; box-shadow: 0 2px 3px rgba(0,0,0,0.25);
  }
  .social-reflection {
    position: absolute; top: 597px; left: 489px; display: flex; gap: 3px;
    opacity: 0.22;
  }
  .social-reflection span {
    width: 54px; height: 44px; border-radius: 0 0 27px 27px;
    background: linear-gradient(var(--green-dark), transparent);
  }

  .footer {
    position: absolute; top: 667px; left: 0; width: 1200px; height: 44px;
    background: var(--green); color: var(--white);
    text-align: center; font-size: 13px; line-height: 44px; letter-spacing: -0.6px;
  }
</style>
</head>
<body>
  <div class="brand">LARKFIELD</div>

  <header class="nav-band">
    <ul class="nav">
      <li class="current">HOME</li>
      <li>ABOUT US</li>
      <li>TREATMENTS</li>
      <li>SERVICES</li>
      <li>CASE STUDIES</li>
      <li>CONTACT US</li>
    </ul>
  </header>

  <section class="feature about">
    <div class="shadow"></div>
    <div class="artwork" role="img" aria-label="Illustration of a green leaf with dew drops"></div>
    <div class="disc">
      <h2>ABOUT US</h2>
      <p>Larkfield Advisory is a highly professional, ethically bound business, with the needs of the client at the forefront of all we do.</p>
      <a class="more" href="#">READ MORE</a>
    </div>
  </section>

  <section class="feature quote-card">
    <div class="shadow"></div>
    <div class="artwork" role="img" aria-label="Illustration of a green leaf with dew drops"></div>
    <div class="disc">
      <p class="quote">“Just living is not enough, one must have sunshine, freedom, and a little flower”</p>
      <p class="author">HELENA MARSH</p>
    </div>
  </section>

  <section class="feature services">
    <div class="shadow"></div>
    <div class="artwork" role="img" aria-label="Illustration of a green leaf with dew drops"></div>
    <div class="disc">
      <h2>SERVICES</h2>
      <p>Psychotherapy &amp; Counselling Practice, Wellness Programs, Individual clients, Corporate services</p>
      <a class="more" href="#">READ MORE</a>
    </div>
  </section>

  <nav class="social" aria-label="Social links">
    <a class="icon" href="#" aria-label="Social link 1"></a>
    <a class="icon" href="#" aria-label="Social link 2"></a>
    <a class="icon" href="#" aria-label="Social link 3"></a>
    <a class="icon" href="#" aria-label="Social link 4"></a>
  </nav>
  <div class="social-reflection" aria-hidden="true">
    <span></span><span></span><span></span><span></span>
  </div>

  <footer class="footer">© 2013 LARKFIELD.</footer>
</body>
</html>
```